Website for a company offering full serivce charging solutions for electric cars

The company "tanu-werk" (english: "tanu-works") offering all-in-one-solutions for charging infrastructure for electric mobility.

There are four products:
1- Wallboxes for single-family homes
2- Solutions for property devloper/-management for property parking space
3- All-in-one-charging solution for municipalities/communities
4- Solutions for tourism/hotels/holiday appartments

The Website structure:
1. Main Page
2.1. Product Page Single Homes
2.2. Product Page Property Management / Parking
2.3. Product Page Municipality
2.4. Product Page Tourism
3. Contact Form / Request for information
4. Imprint / Legal

The Website should be built on Wordpress with a powerful possibility to simply add/modify specific landing pages.

We would like you to implement the website later and also maintain it if possible, but we would be able to do minor modifications by ourselfs (for A/B-Testing)

The website should be clear and simple, easy to understand.
Target group is mainly B2C without deeper knowledge of that topic.

It should suggest, that we will provide a very simple way to get the charging infrastructure done.

We need a contact form, maybe we will use Hubspot later.

Attached you will find a draft of the main page and a landing page (for 2.2) - it is just the content, please ignore the design. We would love to let you create a suitable design.
Also you will find some drafts a bit different for the same story.

I added also a few stock photos, but they don't need to be used! If you have better ideas, you are welcome!

Industry/Entity Type

Charging/Electric mobility

Number of Pages Required

2 page

Font styles to use
Sans Serif

Requirements
Must have
• Based on Wordpress, and the designer should be able to implement it on Wordpress on a later step

```html
<!DOCTYPE html>
<html lang="de">
<head>
<meta charset="utf-8">
<title>tanu-werk – Ladeinfrastruktur für Elektromobilität</title>
<link href="https://fonts.googleapis.com/css2?family=Audiowide&family=Nunito:wght@400;600;700&display=swap" rel="stylesheet">
<style>
:root{
  --navy:#1b2338;
  --navy-deep:#121a2c;
  --navy-band:#2c3653;
  --pink:#e5168f;
  --purple:#8a4bd1;
  --white:#ffffff;
  --text:#d9dcea;
  --grad:linear-gradient(90deg,var(--pink),var(--purple));
}
*{margin:0;padding:0;box-sizing:border-box}
html,body{width:1200px;height:3731px;overflow:hidden}
body{background:var(--navy);color:var(--text);font-family:"Nunito",sans-serif;position:relative}
.abs{position:absolute}
h1,h2,.brand{font-family:"Audiowide",sans-serif;color:var(--white);font-weight:400}
.btn{display:inline-block;background:var(--grad);color:var(--white);font-family:"Audiowide",sans-serif;font-size:12px;letter-spacing:.5px;border-radius:22px;text-decoration:none;text-align:center}
.btn-outline{display:inline-block;border:2px solid var(--pink);color:var(--white);font-family:"Audiowide",sans-serif;font-size:11px;border-radius:20px;padding:9px 18px;text-decoration:none}
/* header */
.site-header{left:0;top:0;width:1200px;height:110px;z-index:5}
.brand{font-size:21px;color:var(--white);display:flex;align-items:center;gap:8px;text-decoration:none;white-space:nowrap}
.brand-dot{width:12px;height:12px;border-radius:50%;background:var(--pink)}
.site-header .brand{position:absolute;left:160px;top:68px}
.main-nav{position:absolute;left:410px;top:37px;display:flex;gap:32px;font-family:"Audiowide",sans-serif;font-size:11px;color:var(--white)}
.nav-cta{position:absolute;left:930px;top:25px;width:107px;height:36px;line-height:36px}
/* hero */
.hero-photo{left:0;top:0;width:1200px;height:600px;background:radial-gradient(circle at 850px 260px,#3ba2ff 0,#2350b8 12%,#2c2f6a 35%,#1b1d3a 65%,#0e1020 100%)}
.hero-curve{left:0;top:440px;width:1200px;height:180px}
.hero-copy{left:161px;top:214px}
.hero-copy .lead{font-size:19px;color:var(--white)}
.hero-copy h1{font-size:44px;line-height:56px;margin-top:8px}
.hero-copy .btn{margin-top:28px;width:245px;height:43px;line-height:43px}
.scroll-down{left:568px;top:564px;width:64px;height:64px;border-radius:50%;background:#fff;border:6px solid #c9ccd8;display:flex;align-items:center;justify-content:center}
/* partner */
.collage-img{border-radius:20px}
.img-a{left:246px;top:690px;width:226px;height:227px;background:linear-gradient(160deg,#f2b35c,#8a5a3a 55%,#3a2a2a)}
.img-b{left:161px;top:848px;width:191px;height:217px;background:linear-gradient(150deg,#e9edf4,#7fa0d8 55%,#2d5fd6)}
.img-c{left:358px;top:925px;width:229px;height:227px;background:linear-gradient(200deg,#dde3ec,#7a8598 50%,#27313f)}
.partner-copy{left:606px;top:682px;width:440px}
.partner-copy h2{font-size:27px;line-height:42px;white-space:nowrap}
.partner-copy .sub{color:var(--pink);font-weight:700;font-size:16px;line-height:24px;margin:16px 0 12px}
.partner-copy p{font-size:13px;line-height:24px;margin-bottom:9px;color:var(--text)}
.partner-copy .btn-outline{margin-top:8px}
/* offers */
.offers-bg{left:0;top:1243px;width:1200px;height:1927px;background:var(--navy-deep)}
.snake{left:0;top:0;width:1200px;height:3731px;pointer-events:none}
.photo-circle{border-radius:50%}
.ph-private{left:623px;top:1326px;width:420px;height:420px;background:radial-gradient(circle at 65% 45%,#e43a3a 0,#9b2430 30%,#2b2d3d 65%,#141826)}
.ph-business{left:153px;top:1761px;width:434px;height:434px;background:linear-gradient(120deg,#cfd6e0,#8b98aa 45%,#e9eef3 70%,#556070)}
.ph-infra{left:620px;top:2217px;width:420px;height:420px;background:linear-gradient(160deg,#a9b6c4,#e2e7ee 50%,#7d8898)}
.ph-community{left:153px;top:2652px;width:434px;height:434px;background:linear-gradient(140deg,#2b4d8a,#5b86c9 45%,#d8dde6 75%,#b8bfca)}
.offer h2{font-size:30px;line-height:40px;margin-bottom:18px}
.ticks{list-style:none;font-size:13px;line-height:24px;color:var(--text)}
.ticks li{position:relative;padding-left:24px;margin-bottom:8px}
.ticks li svg{position:absolute;left:0;top:5px;width:15px;height:15px}
.ticks .sub{padding-left:56px}
.ticks .sub svg{left:32px}
.offer-private{left:164px;top:1335px;width:410px}
.offer-business{left:596px;top:1793px;width:420px}
.offer-infra{left:160px;top:2250px;width:440px}
.offer-community{left:625px;top:2665px;width:420px}
/* cta band */
.cta-band{left:0;top:3170px;width:1200px;height:354px;background:var(--navy-band)}
.cta-photo{left:0;top:3170px;width:478px;height:354px;background:linear-gradient(100deg,#e9ecf1,#b9c1cc 55%,#3d475f)}
.cta-copy{left:567px;top:3255px}
.cta-copy h2{font-size:34px;line-height:42px}
.cta-copy .btn{margin-top:22px;width:245px;height:40px;line-height:40px}
/* footer */
.site-footer{left:0;top:3524px;width:1200px;height:207px;background:var(--navy)}
.site-footer .brand{position:absolute;left:160px;top:76px}
.footer-nav{position:absolute;left:396px;top:82px;display:flex;gap:42px;font-family:"Audiowide",sans-serif;font-size:11px;color:var(--white)}
.copyright{position:absolute;left:162px;top:177px;font-size:11px;color:var(--white)}
.social{position:absolute;left:910px;top:166px;display:flex;gap:14px}
.social span{width:33px;height:33px;border-radius:50%;border:1.5px solid #fff;display:block}
</style>
</head>
<body>

<div class="abs hero-photo" role="img" aria-label="Ladestecker steckt in einem blau leuchtenden Anschluss eines Elektroautos"></div>
<svg class="abs hero-curve" viewBox="0 0 1200 180" preserveAspectRatio="none" aria-hidden="true">
  <defs><linearGradient id="hg" x1="0" x2="1"><stop offset="0" stop-color="#e5168f"/><stop offset="1" stop-color="#8a4bd1"/></linearGradient></defs>
  <path d="M0 40 Q600 270 1200 50 L1200 180 L0 180 Z" fill="#1b2338"/>
  <path d="M0 40 Q600 270 1200 50" fill="none" stroke="url(#hg)" stroke-width="9"/>
</svg>

<header class="abs site-header">
  <a class="brand" href="#"><span class="brand-dot"></span>tanu-werk.de</a>
  <nav class="main-nav"><span>einfach mehr als laden</span><span>Lösungen</span><span>Unternehmen</span><span>Services</span><span>Karriere</span></nav>
  <a class="btn nav-cta" href="#">Kontakt</a>
</header>

<section class="abs hero-copy">
  <p class="lead">Wir bieten Komplettlösungen für die</p>
  <h1>Ladeinfrastruktur<br>für Elektromobilität</h1>
  <a class="btn" href="#">Kontaktieren Sie uns heute</a>
</section>

<a class="abs scroll-down" href="#" aria-label="Weiter nach unten">
  <svg width="18" height="12" viewBox="0 0 18 12"><path d="M3 3l6 6 6-6" fill="none" stroke="#e5168f" stroke-width="2.5" stroke-linecap="round"/></svg>
</a>

<div class="abs collage-img img-a" role="img" aria-label="Frau mit Smartphone neben einem ladenden Auto bei Sonnenuntergang"></div>
<div class="abs collage-img img-b" role="img" aria-label="Ladestecker in blau beleuchteter Ladebuchse"></div>
<div class="abs collage-img img-c" role="img" aria-label="Hand steckt Ladekabel in ein weißes Auto"></div>

<section class="abs partner-copy">
  <h2>tanu-werk ist Ihr Partner</h2>
  <p class="sub">wenn das Laden nicht nur einfach, sondern die Umsetzung auch aus einer Hand kommen soll</p>
  <p>Wir bieten Lösungen sowohl für Privatkunden, Geschäftskunden als auch Kommunen an, die schnell, fair und ohne Eigenleistung zu einer smarten Ladelösung für E-Fahrzeuge kommen möchten.</p>
  <p>Von der Beratung, über die Installation, Inbetriebnahme bis zur Abrechnung und Wartung bekommen Sie bei tanu-werk alles aus einer Hand. Auf Wunsch vermieten wir auch die Ladetechnik und übernehmen im gewerblichen Bereich die direkte Abrechnung mit dem Nutzer. Für Kommunen bieten wir den kostenfreien Full-Service an und beteiligen die Gemeinden an der Nutzung der Infrastruktur.</p>
  <p>Fragen Sie uns nach der auf Ihre individuellen Bedürfnisse zugeschnittenen Lösung:</p>
  <a class="btn-outline" href="#">Kontaktieren Sie uns heute</a>
</section>

<div class="abs offers-bg"></div>

<div class="abs photo-circle ph-private" role="img" aria-label="Lächelnde Frau lädt ein rotes Elektroauto in einer Garage"></div>
<div class="abs photo-circle ph-business" role="img" aria-label="Weiße Ladesäule vor parkenden Autos"></div>
<div class="abs photo-circle ph-infra" role="img" aria-label="Transparentes Auto zwischen zwei Ladesäulen auf einem Parkplatz"></div>
<div class="abs photo-circle ph-community" role="img" aria-label="Blaues Auto an einer öffentlichen Ladesäule mit orangem Kabel"></div>

<svg class="abs snake" viewBox="0 0 1200 3731" aria-hidden="true">
  <defs>
    <linearGradient id="sg" x1="0" x2="1"><stop offset="0" stop-color="#e5168f"/><stop offset="1" stop-color="#8a4bd1"/></linearGradient>
    <symbol id="tick" viewBox="0 0 16 16"><circle cx="8" cy="8" r="6.5" fill="none" stroke="#e5168f" stroke-width="1.4"/><path d="M4.8 8.2l2.2 2.2 5.5-6" fill="none" stroke="#e5168f" stroke-width="1.6" stroke-linecap="round"/></symbol>
  </defs>
  <path d="M830 1305 C980 1305 1060 1420 1060 1540 C1060 1660 980 1758 870 1758 L370 1758 C230 1758 140 1860 140 1980 C140 2100 230 2202 370 2202 L830 2202 C960 2202 1060 2300 1060 2427 C1060 2550 960 2645 830 2645 L370 2645 C230 2645 140 2745 140 2870 C140 2990 230 3092 370 3092 L1080 3092 Q1100 3092 1100 3070 L1100 2975" fill="none" stroke="url(#sg)" stroke-width="6" stroke-linecap="round"/>
</svg>

<section class="abs offer offer-private">
  <h2>als Privatkunde</h2>
  <ul class="ticks">
    <li><svg><use href="#tick"/></svg>Bestandsanalyse mit umfangreicher Beratung über die Möglichkeiten der Umsetzung</li>
    <li><svg><use href="#tick"/></svg>Prüfung und Übernahme der Anmeldung verfügbarer Fördermöglichkeiten</li>
    <li><svg><use href="#tick"/></svg>Auswahl an smarten Wallbox Lösungen, passend für Ihr Fahrzeug und Ihre Bedürfnisse</li>
    <li><svg><use href="#tick"/></svg>Installation inkl. aller notwendigen Materialien und Tätigkeiten (Durchbrüche, Erdarbeiten, etc.)</li>
    <li><svg><use href="#tick"/></svg>Inbetriebnahme und Einweisung in die Ladetechnik</li>
    <li><svg><use href="#tick"/></svg>Jährlich technische Wartung nach DGUV3</li>
    <li><svg><use href="#tick"/></svg>Reparaturservice, unter Berücksichtigung der geltenden Garantie Ansprüche</li>
  </ul>
</section>

<section class="abs offer offer-business">
  <h2>als Geschäftskunde</h2>
  <ul class="ticks">
    <li><svg><use href="#tick"/></svg>Durchführung einer individuellen Bedarfsanalyse inkl. Ermittlung der Anforderungen für:</li>
    <li class="sub"><svg><use href="#tick"/></svg>Haus- und Immobilienverwaltungen</li>
    <li class="sub"><svg><use href="#tick"/></svg>Dienstleistungs- und Handelsunternehmen</li>
    <li class="sub"><svg><use href="#tick"/></svg>Hotel und Beherbergungsbetriebe</li>
    <li class="sub"><svg><use href="#tick"/></svg>Parkraum- und Parkhausbetreiber</li>
    <li class="sub"><svg><use href="#tick"/></svg>Tourismus, Sport- und Freizeiteinrichtungen</li>
    <li><svg><use href="#tick"/></svg>Planung und Projektierung des Installationsaufwands inkl. Materialverbrauch</li>
    <li><svg><use href="#tick"/></svg>Leasing oder Kauf der Hardware</li>
  </ul>
</section>

<section class="abs offer offer-infra">
  <ul class="ticks">
    <li><svg><use href="#tick"/></svg>Normgerechte Installation der Ladeinfrastruktur inkl. Durchbruch-, Brandschutz- und Erdarbeiten</li>
    <li><svg><use href="#tick"/></svg>Leasing oder Kauf der Hardware</li>
    <li><svg><use href="#tick"/></svg>Bei Bestandsbauten Integration der Ladeinfrastruktur in die Gebäudesystemtechnik und ggf. Anpassung des Netzanschlusses</li>
    <li><svg><use href="#tick"/></svg>Inbetriebnahme der Anlage inkl. Prüf- und Messprotokollen</li>
    <li><svg><use href="#tick"/></svg>Wiederkehrende technische Prüfung der Anlage nach DGUV 3</li>
    <li><svg><use href="#tick"/></svg>Austausch und Reparatur Service</li>
    <li><svg><use href="#tick"/></svg>Unterstützung bei der mtl. Nutzungsabrechnung und Einbindung in Ihre vorhandene Abrechnungssysteme</li>
    <li><svg><use href="#tick"/></svg>ODER direkte Abrechnung mit den Nutzern</li>
  </ul>
</section>

<section class="abs offer offer-community">
  <h2>als Kommune</h2>
  <ul class="ticks">
    <li><svg><use href="#tick"/></svg>Konzeptionierung möglicher Ladeinfrastrukturen innerhalb Ihrer Gemeinde</li>
    <li><svg><use href="#tick"/></svg>Planung und Projektsteuerung inkl. sämtlicher behördlicher Genehmigungsverfahren und Beantragung von Fördermitteln</li>
    <li><svg><use href="#tick"/></svg>Fachgerechte Installation und Inbetriebnahme</li>
    <li><svg><use href="#tick"/></svg>Regelmäßige Wartung gemäß Vorschrif</li>
    <li><svg><use href="#tick"/></svg>Reparatur und Kundenservice</li>
    <li><svg><use href="#tick"/></svg>Direkte Abrechnung mit dem Nutzer</li>
    <li><svg><use href="#tick"/></svg>Beteiligung der Gemeinde am Umsatz</li>
    <li><svg><use href="#tick"/></svg>Möglichkeit der Integration von Bonusprogrammen, mit denen der lokale Einzelhandel beworben wird</li>
  </ul>
</section>

<section class="abs cta-band"></section>
<div class="abs cta-photo" role="img" aria-label="Weißes Elektroauto an einer freistehenden Ladesäule"></div>
<div class="abs cta-copy">
  <h2>Werden Sie unser Partner<br>oder Gastgeber der<br>Ladestation</h2>
  <a class="btn" href="#">Kontaktieren Sie uns heute</a>
</div>

<footer class="abs site-footer">
  <a class="brand" href="#"><span class="brand-dot"></span>tanu-werk.de</a>
  <nav class="footer-nav"><span>AGB</span><span>Datenschutzerklärung</span><span>Impressum</span><span>Kontakt</span><span>Karriere</span><span>Kontakt</span><span>FAQs</span></nav>
  <p class="copyright">©tanu-werk GmbH</p>
  <div class="social" aria-label="Soziale Netzwerke"><span></span><span></span><span></span></div>
</footer>

</body>
</html>
```